Brell Stone Company Business Cards

Front and Back Business Card - logo and text setup - cool design. I need workable photoshop or illustrator files so I can setup each employee card with design that is created
Updates

Hi everyone, thank you for the great entries. Please no more white and blue cards - there are so many already - black and silver only now please. thanks!

Target Market(s)

Construction Industry - Facility Managers

Industry/Entity Type

Construction

Contact Information for Business Card

I really like contemporary simplistic looks - clean neat....not opposed to seeing some black backrounds

Requirements
Must have
• Logo/website address with design on front only - www.brellstone-example.com (logo attached)
• Back:
• Name/Title/Company Address/Phone/email address
Nice to have
• Cool design
Should not have
• Nothing gimmicky like Fire or Water - since we are a Fire Protection company - it has all been done

```html
<!DOCTYPE html>
<html lang="en">
<head>
<meta charset="utf-8">
<title>Brell Stone Company – Business Cards</title>
<link rel="stylesheet" href="https://fonts.googleapis.com/css2?family=Source+Sans+3:wght@400;600;700;800&display=swap">
<style>
  :root {
    --backdrop: #7d8590;
    --silver-card: #e6e8eb;
    --silver-card-edge: #cfd2d6;
    --black: #141517;
    --charcoal: #2a2c30;
    --silver: #b9bdc3;
    --silver-light: #dfe2e6;
    --ink: #1c1d20;
    --ink-soft: #4a4d53;
  }
  * { box-sizing: border-box; margin: 0; padding: 0; }
  html, body {
    width: 1200px; height: 1023px; overflow: hidden;
    background: var(--backdrop);
    font-family: "Source Sans 3", "Myriad Pro", Arial, sans-serif;
  }
  .sheet { position: relative; width: 1200px; height: 1023px; }

  .card {
    position: absolute;
    width: 560px; height: 320px;
    border-radius: 2px;
    box-shadow: 0 10px 28px rgba(20, 26, 40, 0.35);
    overflow: hidden;
  }

  /* Contact side */
  .card--contact {
    left: 70px; top: 110px;
    background: linear-gradient(135deg, var(--silver-light) 0%, var(--silver-card) 50%, var(--silver-card-edge) 100%);
  }
  .card--contact .wordmark {
    position: absolute; left: 40px; top: 46px;
    font-weight: 800; font-size: 48px; letter-spacing: -1px;
    color: var(--ink); line-height: 1;
  }
  .divider {
    position: absolute; left: 40px; right: 34px; top: 128px;
    border-top: 3px dotted var(--ink-soft);
  }
  .contact-list {
    position: absolute; right: 34px; top: 152px;
    list-style: none; text-align: right;
  }
  .contact-list li {
    display: flex; align-items: center; justify-content: flex-end; gap: 8px;
    font-size: 13.5px; color: var(--ink); line-height: 21px;
  }
  .contact-icon { width: 13px; height: 13px; flex: none; }
  .person { position: absolute; left: 40px; top: 152px; }
  .person__name { font-weight: 700; font-size: 19px; color: var(--ink); line-height: 1.1; }
  .person__title { font-size: 14px; color: var(--ink-soft); }
  .address {
    position: absolute; left: 40px; bottom: 30px;
    font-size: 14px; color: var(--ink-soft); line-height: 19px; font-style: normal;
  }

  /* Brand side */
  .card--brand {
    left: 570px; top: 560px;
    background: linear-gradient(120deg, var(--black) 0%, var(--charcoal) 55%, var(--black) 100%);
  }
  .card--brand .wordmark {
    position: absolute; left: 0; right: 0; top: 118px; text-align: center;
    font-weight: 800; font-size: 66px; letter-spacing: -1.5px;
    color: var(--silver); line-height: 1;
  }
  .card--brand .web {
    position: absolute; left: 40px; bottom: 30px;
    font-size: 14px; color: var(--silver);
  }
</style>
</head>
<body>
<main class="sheet">

  <section class="card card--contact" aria-label="Business card, contact side">
    <div class="wordmark">Brell Stone</div>

    <div class="divider"></div>

    <div class="person">
      <p class="person__name">Dana Morrow</p>
      <p class="person__title">Director</p>
    </div>

    <ul class="contact-list">
      <li>(555) 014-2280
        <svg class="contact-icon" viewBox="0 0 16 16" aria-hidden="true"><path fill="#4a4d53" d="M4 1l3 3-2 2c1 2 3 4 5 5l2-2 3 3-2 3C7 15 1 9 1 3z"/></svg>
      </li>
      <li>(555) 014-2281
        <svg class="contact-icon" viewBox="0 0 16 16" aria-hidden="true"><rect x="2" y="5" width="12" height="8" rx="1" fill="#4a4d53"/><rect x="4" y="1" width="8" height="5" fill="#4a4d53"/><rect x="5" y="8" width="6" height="2" fill="#e6e8eb"/></svg>
      </li>
      <li>info@brellstone-example.com
        <svg class="contact-icon" viewBox="0 0 16 16" aria-hidden="true"><rect x="1" y="3" width="14" height="10" rx="1" fill="#4a4d53"/><path d="M1.5 3.5L8 9l6.5-5.5" fill="none" stroke="#e6e8eb" stroke-width="1.3"/></svg>
      </li>
      <li>www.brellstone-example.com
        <svg class="contact-icon" viewBox="0 0 16 16" aria-hidden="true"><circle cx="8" cy="8" r="7" fill="#4a4d53"/><path d="M1 8h14M8 1c-3 3-3 11 0 14M8 1c3 3 3 11 0 14" fill="none" stroke="#e6e8eb" stroke-width="1"/></svg>
      </li>
    </ul>

    <address class="address">
      48 Harbor Works Lane<br>
      Millbrook, NY 10990
    </address>
  </section>

  <section class="card card--brand" aria-label="Business card, brand side">
    <div class="wordmark">Brell Stone</div>
    <p class="web">www.brellstone-example.com</p>
  </section>

</main>
</body>
</html>
```